Web Design Project

Bolt-Turn Dakota locksmiths are experts in the residential and
commercial Locksmith industry with over 20 year’s experience.
Our mission is to provide you the best service at the lowest price.
We accomplish our mission with our competitive up-front pricing, we are fast and reliable, providing superior customer service and backing up our work. Your satisfaction is always our top priority.
You can learn a lot about our companies at www.swiftlatchco.example and www.boltturndakota.example.  Other great site for you to look at is www.tumblr-pin.example, this is a site that we would like to be like.
We want a bold, clean site that gets our point across about the ease of re-keying your house and the security that comes with the knowledge that you are the only one that has keys to it.
All content can be taken from the www.boltturndakota.example.

Target Market(s)
Home Owners - Commercial Building Owners Age: 28-70 both men and women
Industry/Entity Type
Residential
Requirements
Must have
- We want to use the colors of orange, black and grey.  You will find our logo on both of the sites.  The main site to focus on is www.boltturndakota.example, this is the site where we will use the design you create.
Please leave a space on the home page for a ClipStream video in the center of the page. Include a place for Friendbook, Chirpnet, JobLoop and Rateit links.
We also would like a strong call to action to call us or go to the ordering page for service.
Must have the home page, contact us page and an typical design template for the other pages.

```html
<!DOCTYPE html>
<html lang="en">
<head>
<meta charset="utf-8">
<title>Bolt-Turn Dakota – Contact Us</title>
<link href="https://fonts.googleapis.com/css2?family=PT+Sans:wght@400;700&family=Arimo:wght@400;700&display=swap" rel="stylesheet">
<style>
:root{
  --bg-dark:#1b1b1b;
  --bg-pattern:#242424;
  --card:#ffffff;
  --orange:#f7941d;
  --orange-deep:#e9780a;
  --orange-light:#fba94a;
  --ink:#2b2b2b;
  --grey:#5a5a5a;
  --grey-soft:#8a8a8a;
  --line:#9c9c9c;
  --slider:#252525;
}
*{box-sizing:border-box;margin:0;padding:0}
html,body{width:1026px;height:1200px;overflow:hidden}
body{background:radial-gradient(circle at 50% 40%,var(--bg-pattern),var(--bg-dark) 75%);font-family:"Arimo",Arial,sans-serif;color:var(--ink)}
.stage{position:absolute;left:0;top:0;width:1000px;height:1170px;transform:scale(1.026);transform-origin:0 0}
.abs{position:absolute}

.page{left:52px;top:42px;width:904px;height:1055px;background:var(--card);border-radius:6px;box-shadow:0 0 8px rgba(0,0,0,.5)}

.header-photo{left:52px;top:42px;width:904px;height:142px;border-radius:6px 6px 0 0;
  background:linear-gradient(90deg,#f4f4f4 0%,#e6e8ea 30%,#cfd4d8 60%,#b9c0b4 85%,#9aa48a 100%)}
.brand-mark{left:74px;top:102px;display:flex;align-items:center;gap:8px;font-family:"PT Sans",sans-serif;font-weight:700;font-size:19px;line-height:22px;color:var(--orange-deep);white-space:nowrap}
.brand-dot{display:block;flex:0 0 22px;width:22px;height:22px;border-radius:50%;background:var(--orange)}
.site-title{left:264px;top:60px;font-family:"PT Sans",sans-serif;font-size:34px;color:var(--ink);white-space:nowrap}
.site-by{left:338px;top:112px;font-family:"PT Sans",sans-serif;font-size:17px;color:var(--ink);white-space:nowrap}
.site-tagline{left:282px;top:147px;font-family:"PT Sans",sans-serif;font-size:17px;color:var(--ink);white-space:nowrap}
.call-label{left:814px;top:86px;font-family:"PT Sans",sans-serif;font-size:18px;color:var(--ink);white-space:nowrap}
.call-number{left:788px;top:116px;font-family:"PT Sans",sans-serif;font-size:23px;color:var(--orange-deep);white-space:nowrap}

.nav{left:58px;top:184px;width:892px;height:38px;border-radius:4px;background:linear-gradient(var(--orange-light),var(--orange-deep))}
.nav a{position:absolute;font-size:13px;color:#111;text-decoration:none;top:12px;white-space:nowrap}
.nav a.active{top:3px;height:31px;padding:8px 11px;background:linear-gradient(#fff,#e4e4e4);border-radius:5px;box-shadow:0 1px 3px rgba(0,0,0,.4)}

.slider-frame{left:59px;top:233px}
.slide-photo{left:75px;top:245px;width:859px;height:318px;
  background:linear-gradient(90deg,#9a6a2a 0%,#d9a44c 25%,#c88a3a 55%,#7a3e22 75%,#5a2c1a 100%)}
.slide-caption{left:75px;top:340px;width:280px;height:125px;background:rgba(20,16,12,.78);padding:20px 12px;font-family:"PT Sans",sans-serif;color:#fff;white-space:nowrap}
.slide-caption .kicker{font-size:19px}
.slide-caption .price{font-size:32px;color:var(--orange);line-height:1}
.slide-caption .sub{font-size:19px;margin-top:8px}
.pager-dot{position:absolute;top:579px;width:17px;height:17px;border-radius:50%}
.pager-dot.on{background:radial-gradient(circle at 40% 35%,#fff,#bbb)}
.pager-dot.off{background:radial-gradient(circle at 40% 35%,#ffc061,var(--orange-deep))}

.contact-title{left:94px;top:649px;font-family:"PT Sans",sans-serif;font-size:22px;font-weight:400;line-height:26px}
.contact-rule{left:94px;top:678px;width:303px;border-top:1px dotted #555}
.contact-intro{left:101px;top:701px;font-size:16px;color:var(--grey);white-space:nowrap}
.field-label{font-size:13px;color:var(--grey);left:101px;white-space:nowrap}
.field{left:98px;width:279px;height:26px;border:1px solid #a7a7a7;border-radius:2px;background:#fff;box-shadow:inset 0 1px 2px rgba(0,0,0,.12)}
.field.comment{height:46px}
.submit{left:264px;top:1037px;width:113px;height:33px;border-radius:4px;background:linear-gradient(var(--orange-light),var(--orange-deep));font-size:14px;color:#111;display:flex;align-items:center;justify-content:center}
.divider{left:437px;top:750px;height:300px;border-left:1px dotted #555}
.map{left:478px;top:767px;width:255px;height:254px;background:linear-gradient(135deg,#e8e5de,#dcd8cf);border:2px solid #eee;outline:1px solid #ccc}
.details-icon{left:760px;top:815px;width:28px;height:28px;border-radius:4px;background:#3a3a3a}
.details-title{left:795px;top:820px;font-size:14px;color:#333;letter-spacing:.3px;white-space:nowrap}
.details-text{left:763px;font-size:12px;color:var(--grey);line-height:21px;white-space:nowrap}

.social{left:62px;top:1122px;display:flex;gap:5px}
.social span{width:21px;height:21px;border-radius:3px;background:linear-gradient(#5aa9e6,#2b6cb0)}
.footer-links{right:50px;top:1110px;font-size:11px;color:#bbb;text-align:right;white-space:nowrap}
.footer-copy{right:50px;top:1134px;font-size:11px;color:#bbb;white-space:nowrap}
</style>
</head>
<body>
<div class="stage">
  <div class="abs page"></div>
  <div class="abs header-photo" role="img" aria-label="Soft photo of a suburban house front"></div>
  <div class="abs brand-mark"><span class="brand-dot"></span><span class="brand-name">Swift Latch Co</span></div>
  <div class="abs site-title">Bolt-Turn Dakota</div>
  <div class="abs site-by">by Swift Latch Co</div>
  <div class="abs site-tagline">"The smarter way to Security"</div>
  <div class="abs call-label">Call us now</div>
  <div class="abs call-number">555-014-2250</div>

  <nav class="abs nav">
    <a style="left:32px">Home</a>
    <a style="left:103px">About Us</a>
    <a style="left:189px">Rekey Special</a>
    <a style="left:305px">Services</a>
    <a style="left:387px">Property Manager</a>
    <a style="left:523px">Commercial Property</a>
    <a style="left:678px">Order Services</a>
    <a class="active" style="left:786px">Contact Us</a>
  </nav>

  <svg class="abs slider-frame" width="892" height="392" viewBox="0 0 892 392">
    <path d="M0 0H890V346Q700 335 560 365Q445 392 330 372Q170 340 0 350Z" fill="#252525"/>
    <path d="M0 350Q170 340 330 372Q445 392 560 365Q700 335 890 346" fill="none" stroke="#555" stroke-width="1"/>
  </svg>
  <div class="abs slide-photo" role="img" aria-label="Photo of brass door lock and handle on a wooden door beside a fruit basket"></div>
  <div class="abs slide-caption">
    <div class="kicker">The Dakota Rekey Special</div>
    <div class="price">$89.95</div>
    <div class="sub">Rekey Any Home</div>
  </div>
  <div class="pager">
    <span class="pager-dot on" style="left:467px"></span>
    <span class="pager-dot off" style="left:497px"></span>
    <span class="pager-dot off" style="left:527px"></span>
  </div>

  <h1 class="abs contact-title">Contact Us</h1>
  <div class="abs contact-rule"></div>
  <p class="abs contact-intro">Kindly post your valuable Suggestions &amp; Query</p>

  <label class="abs field-label" style="top:741px">Enter Your Name</label>
  <div class="abs field" style="top:762px"></div>
  <label class="abs field-label" style="top:815px">Enter Your Email</label>
  <div class="abs field" style="top:833px"></div>
  <label class="abs field-label" style="top:886px">Enter Your Phone Number</label>
  <div class="abs field" style="top:905px"></div>
  <label class="abs field-label" style="top:957px">Add Your Comment Here</label>
  <div class="abs field comment" style="top:976px"></div>
  <div class="abs submit">Submit</div>

  <div class="abs divider"></div>
  <div class="abs map" role="img" aria-label="Street map showing the shop location"></div>

  <div class="abs details-icon">
    <svg width="28" height="28" viewBox="0 0 28 28"><path d="M10 6c-2 1-3 3-2 6 1 4 4 8 8 10 2 1 4 0 5-2l-3-3-2 1c-2-1-4-3-5-5l1-2z" fill="#fff"/></svg>
  </div>
  <div class="abs details-title">CONTACT DETAILS</div>
  <div class="abs details-text" style="top:856px">Bolt-Turn Dakota for the<br>Tri-County and Surrounding Areas</div>
  <div class="abs details-text" style="top:919px">Phone : 555-014-2250<br>Email: info@swiftlatchco.example<br>Fax: 555-016-1519</div>

  <div class="abs social"><span></span><span></span><span></span><span></span></div>
  <div class="abs footer-links">Privacy &amp; Legal &nbsp;|&nbsp; Site Map &nbsp;|&nbsp; Contact Us</div>
  <div class="abs footer-copy">© 2012 Bolt-Turn Dakota. All rights reserved</div>
</div>
</body>
</html>
```